Business card for a new innovative and professional lawn care business

We need a business card design for a new lawn care business in Halifax NS Canada. We offer lawn services in Halifax & Bedford. Our services offered include lawn care, garden services, and property maintenance. We take pride in our work and are experienced at what we do. I would like to see a design that is double sided. On the backside I would like the something simple (maybe my logo preferably on blackround (linked below) with website link, Facebook page or something). The front I want to include contact info:
Morgan Pell
phone 902-555-0148
email - brookvaleyards.ca
facebook - Facebook.com/brookvaleyards
Instagram maybe ? - instagram.com/brookvaleyard
Serving Halifax and Bedford for 5 years?
I don't want it to have too much information as I will be passing them out in aim to visit website, or call !
We do want it to include lawn care, garden services and property maintenance.
Basic, catchy, and modern looking !
Logo attached below !

Target Market(s)

Passing business cards to everyone I meet or interact with.

Industry/Entity Type

Lawn Care

Contact Information for Business Card

Double sided with some basic information, with catchy colours and easy to look at.

Font styles to use
Sans Serif

Requirements
Must have
• Must be double sided and have :
• Name, Phone, Email, FB, Website, and 3 main services offered - lawn care, property maintenance, garden services
Nice to have
• Would be nice to have instagram link if it goes well on there
Should not have
• Don't want too much writing or images that are distracting

```html
<!DOCTYPE html>
<html lang="en">
<head>
<meta charset="utf-8">
<title>Brookvale Yards – Business Card</title>
<link rel="stylesheet" href="https://fonts.googleapis.com/css2?family=Open+Sans:wght@400;600;700&display=swap">
<style>
  :root {
    --page: #ecebe6;
    --card: #ffffff;
    --lime: #8cc63f;
    --lime-light: #a5d65a;
    --forest: #1f7a3a;
    --forest-dark: #16612c;
    --ink: #3a3a3a;
    --white: #ffffff;
  }
  * { margin: 0; padding: 0; box-sizing: border-box; }
  html, body {
    width: 1200px; height: 950px; overflow: hidden;
    background: var(--page);
    font-family: "Open Sans", Arial, sans-serif;
  }
  .sheet {
    position: relative; width: 1200px; height: 950px;
    display: flex; flex-direction: column; align-items: center; justify-content: center; gap: 60px;
  }
  .card {
    position: relative; width: 600px; height: 343px;
    background: var(--card);
    box-shadow: 0 6px 18px rgba(0,0,0,.18);
    overflow: hidden;
  }
  .card-front .band { position: absolute; inset: 0; }
  .brand {
    position: absolute; left: 44px; top: 150px;
    display: flex; align-items: center; gap: 12px;
  }
  .brand-dot { width: 22px; height: 22px; border-radius: 50%; background: var(--forest); }
  .brand-name {
    font-weight: 700; font-size: 30px; color: var(--forest);
    letter-spacing: .5px;
  }
  .contact {
    position: absolute; right: 28px; top: 44px;
    list-style: none; text-align: right; color: var(--white);
  }
  .contact .person { font-size: 21px; font-weight: 600; margin-bottom: 12px; padding-right: 26px; }
  .contact li.line {
    display: flex; align-items: center; justify-content: flex-end; gap: 8px;
    font-size: 13.5px; margin-bottom: 7px;
  }
  .icon {
    width: 16px; height: 16px; flex: none;
    display: flex; align-items: center; justify-content: center;
  }
  .icon-plain { background: var(--white); border-radius: 3px; }
  .mower-art {
    position: absolute; right: 40px; top: 50px; width: 300px; height: 200px;
  }
  .services {
    position: absolute; left: 36px; bottom: 34px;
    display: flex; gap: 22px; list-style: none;
    font-size: 16px; color: var(--ink);
  }
  .services li { display: flex; align-items: center; gap: 6px; }
</style>
</head>
<body>
<main class="sheet">

  <section class="card card-front" aria-label="Business card front">
    <svg class="band" viewBox="0 0 600 343" preserveAspectRatio="none" aria-hidden="true">
      <path d="M230 0 C330 40 400 160 420 343 L600 343 L600 0 Z" fill="var(--lime)"/>
      <path d="M230 0 C330 40 400 160 420 343 L438 343 C420 160 350 40 262 0 Z" fill="var(--forest)"/>
      <path d="M262 0 C350 40 420 160 438 343 L446 343 C428 160 360 40 276 0 Z" fill="var(--white)"/>
    </svg>
    <div class="brand">
      <span class="brand-dot"></span>
      <span class="brand-name">Brookvale Yards</span>
    </div>
    <ul class="contact">
      <li class="person">Morgan Pell</li>
      <li class="line">902-555-0148
        <span class="icon"><svg width="14" height="14" viewBox="0 0 24 24"><path fill="#fff" d="M6.6 10.8a15 15 0 0 0 6.6 6.6l2.2-2.2a1 1 0 0 1 1-.25 11.4 11.4 0 0 0 3.6.57 1 1 0 0 1 1 1V20a1 1 0 0 1-1 1A17 17 0 0 1 3 4a1 1 0 0 1 1-1h3.5a1 1 0 0 1 1 1c0 1.25.2 2.45.57 3.57a1 1 0 0 1-.25 1z"/></svg></span>
      </li>
      <li class="line">info@brookvaleyards.ca
        <span class="icon"><svg width="15" height="12" viewBox="0 0 15 12"><rect x=".5" y=".5" width="14" height="11" rx="1.5" fill="#fff"/><path d="M1 1.5 7.5 7 14 1.5" stroke="var(--lime)" stroke-width="1.3" fill="none"/></svg></span>
      </li>
      <li class="line">brookvaleyards <span class="icon icon-plain"></span></li>
      <li class="line">brookvaleyard <span class="icon icon-plain"></span></li>
    </ul>
  </section>

  <section class="card card-back" aria-label="Business card back">
    <div class="mower-art" role="img" aria-label="Green lawn mower illustration">
      <svg width="300" height="200" viewBox="0 0 300 200" aria-hidden="true">
        <rect x="0" y="0" width="300" height="200" rx="18" fill="var(--forest)" opacity=".9"/>
      </svg>
    </div>
    <ul class="services">
      <li><svg width="14" height="14" viewBox="0 0 14 14"><path d="M1 7 5 11 13 2" stroke="var(--lime)" stroke-width="2.4" fill="none"/></svg>Property Maintenance</li>
      <li><svg width="14" height="14" viewBox="0 0 14 14"><path d="M1 7 5 11 13 2" stroke="var(--lime)" stroke-width="2.4" fill="none"/></svg>Garden Services</li>
    </ul>
  </section>

</main>
</body>
</html>
```